Music Marketing Agency in need of a fully responsive website

Need a website for our music marketing agency with a nice Rev slider has the ability to take payments has a section with our work and client able to see case studies able to download our media kit in PDF can take appointments has social media and a careers upload section. Also want a prominent contact form. Nice and icons for music industry. I want them to be able to download a free Picsandra marketing download Very clean and not large icons or menu at the top very minimal menu bar this will have to go with our logo as well which I will add to order. I want this to be a membership oriented site. so there will be packages displayed or a membership form which they can use to sign up and need a login window. Also need to be able to put Tunevox playlist on the website. Save a section for past clients logos.Again this has to be a clean concept I would like pictures of Quellos such as an app promotion. Definitely want lots of flash words in bold letters across the pages when they scroll through new sections.
Updates

Need extra days to review

Target Market(s)

Urban Music

Coding

Coded - Design and coding required

Font styles to use
Serif

Colors

Designer to choose colors to be used in the design.

Requirements
Must have
• Please Add Logos attached at the Footer

```html
<!DOCTYPE html>
<html lang="en">
<head>
<meta charset="utf-8">
<title>Tessaro Collective – Login</title>
<link href="https://fonts.googleapis.com/css2?family=Bebas+Neue&family=Arimo:wght@400&display=swap" rel="stylesheet">
<style>
  :root {
    --brand-green: #76c01e;
    --modal-bg: #ffffff;
    --field-border: #c9c9c9;
    --label-grey: #6e6e6e;
    --icon-grey: #9a9a9a;
    --close-bg: #111111;
    --footer-bg: #161616;
    --footer-text: #ffffff;
  }
  * { box-sizing: border-box; margin: 0; padding: 0; }
  html, body { width: 1200px; height: 775px; overflow: hidden; }
  body { position: relative; font-family: "Arimo", Arial, sans-serif; background: var(--footer-bg); }

  .hero-photo {
    position: absolute; left: 0; top: 0; width: 1200px; height: 713px;
    background:
      radial-gradient(ellipse at 30% 35%, rgba(70,40,35,0.55), transparent 55%),
      radial-gradient(ellipse at 78% 45%, rgba(75,38,28,0.55), transparent 55%),
      linear-gradient(180deg, #242220 0%, #1e1b19 55%, #2a2622 100%);
  }

  .login-modal {
    position: absolute; left: 354px; top: 149px; width: 493px; height: 425px;
    background: var(--modal-bg); border-radius: 3px;
  }
  .login-title {
    position: absolute; left: 0; right: 0; top: 47px; text-align: center;
    font-family: "Arimo", Arial, sans-serif; font-weight: 400; font-size: 30px; line-height: 1;
    color: var(--brand-green); letter-spacing: 1px;
  }
  .login-field {
    position: absolute; left: 33px; width: 429px; height: 51px;
    border: 1px solid var(--field-border); border-radius: 3px;
    display: flex; align-items: center;
  }
  .login-field.name { top: 117px; }
  .login-field.email { top: 178px; }
  .login-field.password { top: 238px; }
  .field-label { flex: 1; padding-left: 21px; font-size: 12px; color: var(--label-grey); }
  .field-icon {
    width: 46px; height: 16px; border-left: 1px solid var(--field-border);
    display: flex; align-items: center; justify-content: center;
  }
  .field-icon svg { fill: var(--icon-grey); }

  .login-button {
    position: absolute; left: 177px; top: 314px; width: 138px; height: 45px;
    background: var(--brand-green); border-radius: 3px; color: #fff;
    font-family: "Bebas Neue", Impact, sans-serif; font-size: 24px;
    display: flex; align-items: center; justify-content: center; padding-top: 3px;
  }

  .close-button {
    position: absolute; left: 822px; top: 126px; width: 54px; height: 54px;
    border-radius: 50%; background: var(--close-bg); border: 2px solid #fff;
    color: #fff; font-family: "Arimo", Arial, sans-serif; font-weight: 700; font-size: 19px;
    display: flex; align-items: center; justify-content: center;
  }

  .site-footer {
    position: absolute; left: 0; top: 713px; width: 1200px; height: 62px;
    background: var(--footer-bg); color: var(--footer-text);
    display: flex; align-items: center; justify-content: center; font-size: 11px;
  }
</style>
</head>
<body>
  <div class="hero-photo" role="img" aria-label="Dimmed photo of a creative team working together at a table"></div>

  <div class="login-modal">
    <h1 class="login-title">TESSARO COLLECTIVE</h1>

    <div class="login-field name">
      <span class="field-label">Name :</span>
      <span class="field-icon">
        <svg width="10" height="11" viewBox="0 0 10 11"><circle cx="5" cy="3" r="2.7"/><path d="M0 11c0-3.3 2-5 5-5s5 1.7 5 5z"/></svg>
      </span>
    </div>

    <div class="login-field email">
      <span class="field-label">Email :</span>
      <span class="field-icon">
        <svg width="13" height="10" viewBox="0 0 13 10"><path d="M0 0h13v1.6L6.5 5.6 0 1.6z"/><path d="M0 3.2l6.5 4 6.5-4V10H0z"/></svg>
      </span>
    </div>

    <div class="login-field password">
      <span class="field-label">Password :</span>
      <span class="field-icon">
        <svg width="9" height="11" viewBox="0 0 9 11"><path d="M2 5V3.3a2.5 2.5 0 0 1 5 0V5h-1.3V3.3a1.2 1.2 0 0 0-2.4 0V5z"/><rect x="0" y="5" width="9" height="6" rx="1"/></svg>
      </span>
    </div>

    <div class="login-button">Login</div>
  </div>

  <div class="close-button">x</div>

  <footer class="site-footer">© Copyright-2018 Tessaro Collective. All rights reserved.</footer>
</body>
</html>
```